Harborlight Amusement Collective (HAC)

We need a business card design for Harborlight Amusement Collective. Modern and sleek looking, with all critical information. Open to single or double sided designs, if double sided info needs to be all on one side. The main Logo is Harborlight Amusement collective and must be on the card. The other three logos are for the brands that fall under the group, they might be good on the back.

Industry/Entity Type

Business

```html
<!DOCTYPE html>
<html lang="en">
<head>
<meta charset="utf-8">
<title>Harborlight Amusement Collective – Business Card</title>
<link rel="stylesheet" href="https://fonts.googleapis.com/css2?family=Montserrat:wght@400;500;600;700&family=Exo+2:wght@600&display=swap">
<style>
  :root {
    --backdrop: #e3e3e3;
    --card: #ffffff;
    --blue: #2456a0;
    --green: #86a73a;
    --ink: #2b2b2b;
    --muted: #666666;
    --rule: #b8c98a;
  }
  * { box-sizing: border-box; margin: 0; padding: 0; }
  html, body { width: 1200px; height: 852px; overflow: hidden; }
  body {
    background: var(--backdrop);
    font-family: "Montserrat", sans-serif;
    position: relative;
  }
  .card {
    position: absolute;
    top: 271px;
    width: 540px;
    height: 310px;
    background: var(--card);
    border-radius: 18px;
    overflow: hidden;
    box-shadow: 0 6px 18px rgba(0,0,0,0.18);
  }
  .card--brands { left: 45px; }
  .card--contact { left: 615px; }

  /* Wordmark */
  .wordmark { display: flex; align-items: center; gap: 12px; }
  .wordmark__square { width: 34px; height: 34px; background: var(--blue); flex: none; }
  .wordmark__name {
    color: var(--blue);
    font-weight: 700;
    font-size: 19px;
    line-height: 1.15;
    letter-spacing: 0.5px;
    text-transform: uppercase;
  }

  /* Brands side */
  .card--brands .wordmark { position: absolute; top: 46px; left: 50%; transform: translateX(-50%); }
  .divider {
    position: absolute; left: 40px; right: 40px; height: 2px; background: var(--rule);
  }
  .divider--top { top: 140px; }
  .divider--bottom { top: 262px; }
  .brands-label {
    position: absolute; top: 150px; width: 100%; text-align: center;
    font-size: 12px; color: var(--muted); font-weight: 500;
  }
  .brand-row {
    position: absolute; top: 178px; left: 0; width: 100%;
    display: flex; justify-content: center; align-items: center;
  }
  .brand {
    display: flex; align-items: center; gap: 7px; padding: 0 20px;
    font-weight: 700; font-size: 17px;
  }
  .brand + .brand { border-left: 1.5px solid #aaaaaa; }
  .brand__dot { width: 14px; height: 14px; border-radius: 50%; flex: none; }
  .brand--tix { color: var(--green); }
  .brand--tix .brand__dot { background: var(--green); }
  .brand--boxseat { color: var(--ink); flex-direction: column; gap: 0; align-items: flex-start; }
  .brand--boxseat .brand__sub { font-size: 9px; font-weight: 500; color: var(--blue); }
  .brand--gatepass { color: var(--blue); }
  .brand--gatepass .brand__dot { background: var(--blue); }
  .brand__tld { font-size: 8px; font-weight: 500; color: var(--green); align-self: flex-start; }
  .brands-web {
    position: absolute; top: 230px; width: 100%; text-align: center;
    font-size: 12.5px; color: var(--ink); font-weight: 500;
  }

  /* Contact side */
  .card--contact .wordmark { position: absolute; top: 66px; right: 34px; }
  .card--contact .wordmark__name { font-size: 17px; }
  .wave { position: absolute; inset: 0; width: 540px; height: 310px; }
  .person { position: absolute; top: 58px; left: 34px; }
  .person__name {
    font-family: "Exo 2", sans-serif; font-weight: 600;
    font-size: 22px; color: var(--blue);
  }
  .person__role { font-size: 12.5px; color: var(--ink); margin-top: 2px; font-weight: 500; }
  .contact {
    position: absolute; left: 34px; top: 214px;
    color: #ffffff; font-size: 11.5px; line-height: 1.4;
    font-style: normal;
  }
  .contact__address { margin-bottom: 5px; }
  .contact__list { list-style: none; }
  .contact__item { display: flex; align-items: center; gap: 10px; }
  .contact__icon { width: 11px; height: 11px; fill: #ffffff; flex: none; }
</style>
</head>
<body>

<section class="card card--brands">
  <div class="wordmark">
    <span class="wordmark__square"></span>
    <span class="wordmark__name">Harborlight Amusement<br>Collective</span>
  </div>
  <div class="divider divider--top"></div>
  <p class="brands-label">Our Brands</p>
  <div class="brand-row">
    <div class="brand brand--tix"><span class="brand__dot"></span>HarborTix</div>
    <div class="brand brand--boxseat">Boxseat<span class="brand__sub">Hospitality</span></div>
    <div class="brand brand--gatepass"><span class="brand__dot"></span>gatepass<span class="brand__tld">.net</span></div>
  </div>
  <p class="brands-web">www.harborlightcollective.com</p>
  <div class="divider divider--bottom"></div>
</section>

<section class="card card--contact">
  <svg class="wave" viewBox="0 0 540 310" aria-hidden="true">
    <path fill="var(--green)" d="M0,154 C120,180 300,180 400,150 C470,130 510,124 540,120 L540,134 C510,138 470,146 400,166 C300,196 120,196 0,168 Z"/>
    <path fill="var(--blue)" d="M0,176 C120,204 300,204 400,174 C470,154 510,148 540,144 L540,310 L0,310 Z"/>
  </svg>

  <div class="person">
    <h1 class="person__name">Alex Marlow</h1>
    <p class="person__role">Managing Director</p>
  </div>

  <div class="wordmark">
    <span class="wordmark__square"></span>
    <span class="wordmark__name">Harborlight Amusement<br>Collective</span>
  </div>

  <address class="contact">
    <p class="contact__address">48 Quayside Lane,<br>Bayview, US 104820</p>
    <ul class="contact__list">
      <li class="contact__item">
        <svg class="contact__icon" viewBox="0 0 12 12"><path d="M2.5 0.5 L4.5 0.5 L5.2 3.2 L3.8 4.2 C4.5 5.8 6.2 7.5 7.8 8.2 L8.8 6.8 L11.5 7.5 L11.5 9.5 C11.5 10.6 10.6 11.5 9.5 11.5 C4.5 11.5 0.5 7.5 0.5 2.5 C0.5 1.4 1.4 0.5 2.5 0.5 Z"/></svg>
        555.203.4417
      </li>
      <li class="contact__item">
        <svg class="contact__icon" viewBox="0 0 12 12"><path d="M0.5 2 H11.5 V10 H0.5 Z M1 2.5 L6 6.5 L11 2.5" stroke="var(--blue)" stroke-width="0.9"/></svg>
        alex@harborlightcollective.com
      </li>
      <li class="contact__item">
        <svg class="contact__icon" viewBox="0 0 12 12"><circle cx="6" cy="6" r="5.5"/><path d="M0.5 6 H11.5 M6 0.5 C3 3.5 3 8.5 6 11.5 M6 0.5 C9 3.5 9 8.5 6 11.5" stroke="var(--blue)" stroke-width="0.8" fill="none"/></svg>
        www.harborlightcollective.com
      </li>
    </ul>
  </address>
</section>

</body>
</html>
```